Design material for Lumora Event

We need a design of POSM for Lumora Event
1. Content:
- The Lumora Event 3rd
- Singapore 28.10.2018
- A placeholder for insert logo of sponsors (limit 10 logo)
2. POSM:
- Backdrop: 5,5m and 2,6m
- Banner: 4m and 0,5m
- Standee: 0,8m and 2m
- Cover: A4 size
3. Style:
We need style simply because we are a hospital.
Main color: light blue and a little of green (if can)

Hope to see your design soon!

Font styles to use
Sans Serif

Colors
0792cd
85cae6
86cfc6
33b8a4
33a6d7

```html
<!DOCTYPE html>
<html lang="en">
<head>
<meta charset="utf-8">
<title>Lumora Event 2018</title>
<link href="https://fonts.googleapis.com/css2?family=Montserrat:wght@300;400;500;600;700&family=Open+Sans:wght@300;400;600;700&display=swap" rel="stylesheet">
<style>
  :root {
    --navy-bg: #135e8b;
    --navy-deep: #0f5580;
    --slate-ring: #5a8ca7;
    --sky: #6dcbef;
    --sky-soft: #85cae6;
    --mint: #8dc9a7;
    --teal: #33b8a4;
    --teal-soft: #86cfc6;
    --ink: #2b4677;
    --white: #ffffff;
    --footer-ink: #1f3547;
  }
  * { margin: 0; padding: 0; box-sizing: border-box; }
  html, body { width: 848px; height: 1200px; overflow: hidden; background: #e9eef2; }
  .poster {
    position: relative; width: 848px; height: 1200px; overflow: hidden;
    background: var(--navy-bg);
    font-family: "Montserrat", "Open Sans", sans-serif; color: var(--white);
  }
  .skyline-photo {
    position: absolute; left: 0; top: 0; width: 848px; height: 312px;
    background:
      radial-gradient(ellipse at 78% 55%, rgba(250,214,140,.9) 0%, rgba(250,214,140,0) 40%),
      linear-gradient(180deg, #8c9fb4 0%, #c9d3dc 35%, #7f94a4 62%, #3d5566 100%);
  }
  .shapes { position: absolute; left: 0; top: 0; }
  .edition { position: absolute; left: 130px; top: 238px; width: 170px; text-align: center; font-family: "Open Sans", sans-serif; font-weight: 700; line-height: 1; }
  .edition-number { font-size: 96px; }
  .edition-suffix { font-size: 30px; font-weight: 600; vertical-align: 50px; }
  .event-title { position: absolute; left: 250px; top: 372px; width: 400px; text-align: center; font-family: "Open Sans", sans-serif; line-height: 1; }
  .event-title-name { display: block; font-size: 64px; font-weight: 300; padding-bottom: 12px; border-bottom: 4px solid var(--white); margin: 0 40px; }
  .event-title-kind { display: block; font-size: 64px; font-weight: 700; margin-top: 10px; }
  .event-year { position: absolute; left: 567px; top: 573px; width: 190px; text-align: center; font-family: "Open Sans", sans-serif; font-size: 44px; font-weight: 400; }
  .city { position: absolute; left: 82px; top: 864px; font-size: 24px; font-weight: 600; letter-spacing: 14.5px; color: var(--teal); }
  .weekday { position: absolute; left: 178px; top: 895px; font-size: 54px; font-weight: 300; color: var(--teal-soft); }
  .day { position: absolute; left: 437px; top: 838px; font-size: 112px; font-weight: 300; color: var(--sky-soft); line-height: 1; }
  .month { position: absolute; left: 583px; top: 880px; font-size: 36px; font-weight: 400; color: var(--teal); }
  .time { position: absolute; left: 183px; top: 956px; font-size: 25px; font-weight: 400; }
  .setup-note { position: absolute; left: 307px; top: 959px; font-size: 14px; line-height: 1.35; }
  .contact { position: absolute; left: 454px; top: 962px; }
  .contact-label { font-size: 12px; letter-spacing: .3px; }
  .contact-email { font-size: 19px; margin-top: 2px; }
  .event-blurb { position: absolute; left: 70px; top: 1018px; width: 712px; font-size: 12.6px; line-height: 1.42; text-align: center; }
  .sponsor-strip {
    position: absolute; left: 0; top: 1096px; width: 848px; height: 104px; background: var(--white);
    display: flex; align-items: center; justify-content: space-between; padding: 0 30px;
  }
  .sponsor { display: flex; align-items: center; gap: 5px; font-family: "Montserrat", sans-serif; font-weight: 700; font-size: 10px; line-height: 1.1; color: var(--footer-ink); text-transform: uppercase; text-align: center; }
  .sponsor-dot { width: 10px; height: 10px; border-radius: 50%; background: var(--footer-ink); flex: none; }
  .sponsor-square { width: 10px; height: 10px; background: var(--footer-ink); flex: none; }
</style>
</head>
<body>
<main class="poster">
  <div class="skyline-photo" role="img" aria-label="Photograph of the Singapore waterfront skyline at sunset"></div>

  <svg class="shapes" width="848" height="1200" viewBox="0 0 848 1200" aria-hidden="true">
    <defs>
      <linearGradient id="helixTone" x1="0" y1="0" x2="1" y2="1">
        <stop offset="0" stop-color="#3dbfa9"/>
        <stop offset=".55" stop-color="#6fd0c0"/>
        <stop offset="1" stop-color="#3aa89e"/>
      </linearGradient>
      <clipPath id="stripeClip">
        <rect x="65" y="495" width="170" height="70" rx="35" transform="rotate(-42 150 530)"/>
      </clipPath>
    </defs>

    <circle cx="95" cy="775" r="62" fill="var(--navy-deep)"/>
    <circle cx="690" cy="725" r="88" fill="var(--navy-deep)"/>

    <path d="M 110 450 A 235 235 0 0 1 330 110" fill="none" stroke="var(--sky)" stroke-width="6"/>
    <path d="M 670 350 A 100 100 0 1 1 690 545" fill="none" stroke="var(--mint)" stroke-width="8"/>

    <rect x="-35" y="385" width="930" height="72" rx="36" fill="var(--sky)" transform="rotate(-40 430 421)"/>
    <rect x="500" y="100" width="300" height="62" rx="31" fill="var(--mint)" transform="rotate(-42 650 131)"/>
    <rect x="225" y="595" width="210" height="72" rx="36" fill="var(--mint)" transform="rotate(-42 330 631)"/>
    <rect x="718" y="415" width="110" height="56" rx="28" fill="var(--sky)" transform="rotate(-42 773 443)"/>

    <rect x="65" y="495" width="170" height="70" rx="35" fill="var(--sky-soft)" transform="rotate(-42 150 530)"/>
    <g clip-path="url(#stripeClip)" fill="var(--ink)">
      <rect x="70" y="440" width="14" height="200" transform="rotate(48 150 530)"/>
      <rect x="100" y="440" width="14" height="200" transform="rotate(48 150 530)"/>
      <rect x="130" y="440" width="14" height="200" transform="rotate(48 150 530)"/>
      <rect x="160" y="440" width="14" height="200" transform="rotate(48 150 530)"/>
    </g>

    <rect x="100" y="415" width="62" height="30" rx="15" fill="var(--mint)" transform="rotate(-42 131 430)"/>
    <rect x="520" y="702" width="72" height="46" rx="23" fill="var(--sky)" transform="rotate(-42 556 725)"/>
    <rect x="680" y="706" width="72" height="28" rx="14" fill="var(--mint)" transform="rotate(-42 716 720)"/>
    <circle cx="660" cy="777" r="13" fill="var(--mint)"/>
    <circle cx="215" cy="772" r="18" fill="var(--mint)"/>

    <circle cx="450" cy="455" r="257" fill="var(--slate-ring)"/>
    <circle cx="450" cy="455" r="215" fill="url(#helixTone)" role="img" aria-label="Illustration of a DNA double helix"/>

    <circle cx="215" cy="298" r="86" fill="var(--mint)"/>

    <circle cx="662" cy="600" r="96" fill="var(--sky)"/>
    <circle cx="662" cy="600" r="76" fill="none" stroke="var(--ink)" stroke-width="4"/>
  </svg>

  <div class="edition"><span class="edition-number">3</span><span class="edition-suffix">rd</span></div>

  <h1 class="event-title">
    <span class="event-title-name">Lumora</span>
    <span class="event-title-kind">Event</span>
  </h1>

  <div class="event-year">2018</div>

  <div class="city">SINGAPORE</div>
  <div class="weekday">SUNDAY</div>
  <div class="day">28</div>
  <div class="month">OCTOBER</div>

  <div class="time">6:30pm</div>
  <div class="setup-note">Students set up<br>in the cafeteria</div>
  <div class="contact">
    <div class="contact-label">QUESTIONS? CONTACT</div>
    <div class="contact-email">LumoraEvent@email.com</div>
  </div>

  <p class="event-blurb">At vero eos et accusamus et iusto odio dignissimos ducimus qui blanditiis praesentium voluptatum deleniti atque corrupti quos dolores et quas molestias excepturi sint occaecati cupiditate non provident, similique sunt in culpa qui officia deserunt mollitia animi, id est laborum et dolorum fuga.</p>

  <footer class="sponsor-strip">
    <div class="sponsor">Bluefern<br>Rafting</div>
    <div class="sponsor"><span class="sponsor-square"></span>Tallpine<br>Build</div>
    <div class="sponsor">Meadowlark<br>Farm</div>
    <div class="sponsor"><span class="sponsor-dot"></span>Kestra</div>
    <div class="sponsor">Hearth<br>Craft</div>
    <div class="sponsor">Northbank<br>Paddle Club</div>
    <div class="sponsor">trailwise</div>
    <div class="sponsor">Corrin<br>Spirits</div>
    <div class="sponsor">Westwater<br>Canoe</div>
    <div class="sponsor"><span class="sponsor-square"></span>Ridgeline</div>
  </footer>
</main>
</body>
</html>
```